Employment Agency Website Design

We are working with an employment agency in California.

Some sites to use for content/competitors and inspiration:

https://www.pinecrestjobs.com/us/en
https://www.velmorusa.com
https://www.dravenworks.us
https://www.quillora.com/en
https://www.tomvalusa.com
https://www.fernstaffing.com

Thank you for taking the time to consider designing a website for us. We are web developers based in Stockton, CA, USA. Most of our projects go through the same process. Understanding this process may help you win a project with us. We custom-code all of our websites in-house. We don’t have any requirements as to what tools you use for your design, but we prefer Figma files. For any design that we label as four-stars, we send it to the client for review. The client picks the final design they want us to use. Once we complete this process, we will continue to show additional clients all the four-star sites and purchase them later. Your designs will have multiple chances to sell. For better chances of success, we ask that you follow these guidelines.

IMAGES:
If you use any images or icons in the design, we ask that you have a link to the asset so we can purchase the image/icon. Most of the designs we submit do not have the customer’s images on them unless they have some great images. Be creative; show us the feeling you are trying to portray with your image choices. Use any royalty-free site you choose. We subscribe to Adobe and mainly use their images, but we can purchase images outside of Adobe. PLEASE NOTE: we will not submit designs to clients with watermarks on the images.

FONTS:
We ask that you identify the fonts used in the design. This can be done in a message if you want. We typically use Google Fonts and Adobe Fonts.

CONTENT:
We're always open to different content and ideas. We often submit designs with stock images so the client can see our vision. We typically take pictures after the website launch to use their images with our vision. Lorem Ipsum is fine for paragraphs, but we ask that you write the headers in correct English. We want to be able to show the vision and identify the sections of the website.

INSPIRATION:
We typically add a couple of links in the brief of websites we like to help you get started in your design.

REVISIONS:
We do not often ask for revisions of the designs unless we see something in the design that may not appeal to the client. If there are slight changes that we want to make, we do that in the development process.

FEEDBACK:
We rarely give feedback on designs during the design process. We are working on many website projects and do not have the time to provide feedback. We usually respond if your request is well thought out and asks specific questions, but a note asking “feedback, please” usually goes unanswered.

```html
<!DOCTYPE html>
<html lang="en">
<head>
<meta charset="UTF-8">
<title>Keystep Talent – Employment Agency</title>
<link href="https://fonts.googleapis.com/css2?family=Rubik:wght@500;700&family=Roboto:wght@400;500;700&display=swap" rel="stylesheet">
<style>
:root{
  --red:#c11f2f;
  --red-dark:#a8192a;
  --ink:#222;
  --text:#6b6b6b;
  --grey-band:#f2f2f2;
  --pink:#fbeef0;
  --footer:#262626;
  --footer-deep:#1c1c1c;
  --white:#fff;
}
*{margin:0;padding:0;box-sizing:border-box}
html,body{width:1200px;height:4142px;overflow:hidden}
body{position:relative;font-family:'Roboto',sans-serif;color:var(--ink);background:var(--white)}
.abs{position:absolute}
h1,h2,h3,.heading{font-family:'Rubik',sans-serif}
.accent{color:var(--red)}
a{color:inherit;text-decoration:none}

/* buttons */
.btn{position:absolute;display:flex;align-items:center;justify-content:center;gap:8px;font:700 14px 'Roboto',sans-serif;text-transform:uppercase;letter-spacing:.2px}
.btn-solid{background:var(--red);color:var(--white);box-shadow:3px 3px 0 -1px var(--white),4px 4px 0 0 var(--red)}
.btn-outline{border:2px solid var(--red);color:var(--red);background:var(--white)}
.btn-light{background:var(--white);color:var(--red);box-shadow:3px 3px 0 -1px var(--red),4px 4px 0 0 var(--white)}
.dot-arrow{width:14px;height:14px}

/* top bar */
.topbar{left:386px;top:0;width:814px;height:32px;background:var(--red);clip-path:polygon(0 0,100% 0,100% 100%,22px 100%);color:var(--white);font-size:12px}
.topbar .item{position:absolute;top:9px;display:flex;align-items:center;gap:6px}
.topbar .sep{position:absolute;left:617px;top:8px;width:1px;height:16px;background:rgba(255,255,255,.7)}
.topbar .social{position:absolute;top:11px;width:10px;height:10px;border-radius:50%;background:var(--white)}

/* header */
.header{left:0;top:32px;width:1200px;height:86px}
.brand{position:absolute;left:110px;top:22px;display:flex;align-items:center;gap:8px}
.brand-mark{width:40px;height:40px;border-radius:50%;background:var(--red)}
.brand-name{font:500 32px 'Roboto',sans-serif;color:var(--ink);letter-spacing:-.5px}
.nav{position:absolute;left:393px;top:31px;display:flex;gap:35px;font-size:15px;font-weight:500;color:var(--ink)}

/* hero */
.hero{left:0;top:118px;width:1200px;height:720px;overflow:hidden}
.hero-photo{position:absolute;inset:0;background:linear-gradient(90deg,#6d7176 0%,#8d9196 35%,#aeb2b6 55%,#8a8f97 72%,#c9c6c0 100%)}
.hero-shape{position:absolute;left:0;top:442px;width:1200px;height:278px}
.hero-copy{position:absolute;left:114px;top:152px;color:var(--white)}
.hero-copy .pre{font:700 36px 'Rubik',sans-serif}
.hero-copy h1{font-weight:700;font-size:74px;line-height:1;margin-top:8px;letter-spacing:.5px}
.hero-copy p{font-size:16px;line-height:27px;width:500px;margin-top:26px}

/* about */
.about-visual{left:148px;top:904px;width:377px;height:420px;background:linear-gradient(150deg,#d33a46,#b81c2b 60%,#9c1624)}
.about-copy{left:597px;top:930px;width:492px}
.about-copy h2{font-size:38px;font-weight:700}
.about-copy p{font-size:15px;line-height:26.5px;color:var(--text);margin-top:12px}
.about-copy p + p{margin-top:6px}

/* services */
.services{left:0;top:1404px;width:1200px;height:586px;background:var(--grey-band)}
.section-title{position:absolute;left:0;width:1200px;text-align:center;font:700 38px 'Rubik',sans-serif}
.service{position:absolute;top:150px;width:352px;text-align:center}
.service .icon{display:block;margin:0 auto;width:124px;height:124px}
.service h3{font:500 18px 'Roboto',sans-serif;color:var(--ink);margin-top:26px}
.service p{font-size:14.5px;line-height:24px;color:var(--text);margin:10px auto 0;width:275px}
.service .btn{position:relative;margin:24px auto 0;width:150px;height:42px}
.divider{position:absolute;top:130px;width:1px;height:350px;background:#e0e0e0}

/* find talent */
.talent-photo{left:0;top:1990px;width:620px;height:539px;background:linear-gradient(120deg,#9a8a78,#cdc4b8 40%,#e3ddd4 60%,#8a7a6c)}
.talent-panel{left:620px;top:1990px;width:580px;height:539px;background:var(--red);color:var(--white)}
.talent-panel h2{position:absolute;left:46px;top:86px;font-size:38px;line-height:38px;font-weight:700}
.talent-panel p{position:absolute;left:46px;top:174px;width:422px;font-size:15px;line-height:26.5px;text-align:justify}

/* blog */
.card{position:absolute;top:2681px;width:309px;height:388px;background:var(--white);box-shadow:0 2px 12px rgba(0,0,0,.1);text-align:center}
.card .thumb{margin:8px;height:203px}
.card .meta{font-size:12px;color:var(--red);margin-top:26px}
.card h3{font:500 17px 'Roboto',sans-serif;margin-top:12px}
.card p{font-size:14px;line-height:22px;color:var(--text);width:270px;margin:8px auto 0}
.card .more{display:flex;justify-content:center;align-items:center;gap:7px;color:var(--red);font-weight:700;font-size:14px;margin-top:14px}

/* contact */
.contact{left:0;top:3153px;width:1200px;height:637px;background:linear-gradient(180deg,#fcf1f2,#f7e2e5)}
.field{position:absolute;background:var(--white);border:1px solid #dcdcdc;font-size:13px;color:#8a8a8a;padding:0 20px;display:flex;align-items:center}
.field.area{align-items:flex-start;padding-top:22px}

/* footer */
.footer{left:0;top:3790px;width:1200px;height:296px;background:var(--footer);color:#d8d8d8}
.footer-shape{left:0;top:3600px;width:1200px;height:200px}
.foot-brand{position:absolute;left:110px;top:130px;width:230px;text-align:center}
.foot-brand .mark{width:46px;height:46px;border-radius:50%;background:var(--red);margin:0 auto 14px}
.foot-brand .name{font:500 34px 'Roboto',sans-serif;color:var(--white)}
.foot-col{position:absolute;top:36px}
.foot-col h4{font:700 17px 'Roboto',sans-serif;color:var(--white);text-transform:uppercase}
.foot-col h4::after{content:"";display:block;width:60px;height:2px;background:var(--white);margin-top:10px}
.foot-col ul{list-style:none;margin-top:12px;padding-left:6px}
.foot-col li{font-size:15px;line-height:33.5px}
.contact-line{display:flex;gap:12px;font-size:15px;line-height:19px;margin-top:14px;align-items:flex-start}
.contact-line .ic{flex:none;width:24px;height:24px;border-radius:50%;background:#3a3a3a;display:flex;align-items:center;justify-content:center}
.chat{left:1118px;top:4007px;width:58px;height:58px;border-radius:50%;background:var(--red);display:flex;align-items:center;justify-content:center}
.bottom-bar{left:0;top:4086px;width:1200px;height:56px;background:var(--footer-deep);color:var(--white);font-size:12.5px}
.bottom-bar .copy{position:absolute;left:110px;top:20px}
.bottom-bar .copy u{font-weight:700}
.bottom-bar .circ{position:absolute;top:12px;width:30px;height:30px;border-radius:50%;background:var(--white)}
</style>
</head>
<body>

<!-- top bar -->
<div class="abs topbar">
  <div class="item" style="left:52px">
    <svg width="11" height="11" viewBox="0 0 24 24" fill="#fff"><path d="M6.6 10.8a15.1 15.1 0 0 0 6.6 6.6l2.2-2.2c.3-.3.7-.4 1-.2 1.1.4 2.3.6 3.6.6.6 0 1 .4 1 1V20c0 .6-.4 1-1 1A17 17 0 0 1 3 4c0-.6.4-1 1-1h3.5c.6 0 1 .4 1 1 0 1.3.2 2.5.6 3.6.1.3 0 .7-.2 1z"/></svg>
    +1 888 888 8888
  </div>
  <div class="item" style="left:240px">
    <svg width="12" height="10" viewBox="0 0 24 18" fill="#fff"><path d="M0 0h24v18H0z M2 2v1l10 7 10-7V2z" fill-rule="evenodd"/></svg>
    info@keysteptalent.com
  </div>
  <div class="sep"></div>
  <span class="social" style="left:645px"></span>
  <span class="social" style="left:666px"></span>
  <span class="social" style="left:688px"></span>
</div>

<!-- header -->
<header class="abs header">
  <div class="brand"><span class="brand-mark"></span><span class="brand-name">keysteptalent</span></div>
  <nav class="nav"><a>Home</a><a>About Us</a><a>Services</a><a>Testimonials</a><a>Blog</a><a>Contact Us</a></nav>
  <a class="btn btn-solid" style="left:963px;top:21px;width:120px;height:40px">Login
    <svg width="12" height="13" viewBox="0 0 24 26" fill="#fff"><circle cx="12" cy="7" r="6"/><path d="M1 26c0-7 5-11 11-11s11 4 11 11z"/></svg>
  </a>
</header>

<!-- hero -->
<section class="abs hero">
  <div class="hero-photo" role="img" aria-label="Professional woman on the phone working at a laptop in a bright office"></div>
  <div class="hero-copy">
    <div class="pre">Welcome To</div>
    <h1>Keystep Talent</h1>
    <p>Lorem ipsum dolor sit amet, consectetur adipiscing elit, sed do eiusmod tempor incididunt ut labore et dolore magna aliqua.</p>
  </div>
  <a class="btn btn-solid" style="left:114px;top:380px;width:157px;height:48px">Get Started
    <svg class="dot-arrow" viewBox="0 0 16 16"><circle cx="8" cy="8" r="8" fill="#fff"/><path d="M6.5 4.5 10 8l-3.5 3.5" stroke="#c11f2f" stroke-width="2" fill="none"/></svg>
  </a>
  <svg class="hero-shape" viewBox="0 0 1200 278" preserveAspectRatio="none">
    <path d="M0 96 Q600 262 1200 96 L1200 278 L0 278 Z" fill="#fff"/>
    <path d="M30 112 L600 252 L1170 112 L600 205 Z" fill="#c11f2f"/>
    <circle cx="600" cy="212" r="30" fill="#fff" stroke="#c11f2f" stroke-width="4"/>
  </svg>
</section>

<!-- about -->
<div class="abs about-visual" role="img" aria-label="Brand illustration with a red team photo tint"></div>
<section class="abs about-copy">
  <h2>About <span class="accent">Us</span></h2>
  <p>Lorem ipsum dolor sit amet, consectetur adipiscing elit, sed do eiusmod tempor incididunt ut labore et dolore magna aliqua. Ut enim ad minim veniam, quis nostrud exercitation ullamco laboris nisi ut aliquip ex ea commodo consequat. Duis aute irure dolor in reprehenderit in voluptate velit esse cillum dolore eu fugiat nulla pariatur. Excepteur sint occaecat cupidatat non proident, sunt in culpa qui officia deserunt.</p>
  <p>Duis aute irure dolor in reprehenderit in voluptate velit esse cillum dolore eu fugiat nulla pariatur. Excepteur sint occaecat cupidatat non proident, sunt in culpa qui officia deserunt mollit anim id est laborum</p>
</section>
<a class="btn btn-solid" style="left:598px;top:1240px;width:157px;height:48px">Learn More
  <svg class="dot-arrow" viewBox="0 0 16 16"><circle cx="8" cy="8" r="8" fill="#fff"/><path d="M6.5 4.5 10 8l-3.5 3.5" stroke="#c11f2f" stroke-width="2" fill="none"/></svg>
</a>

<!-- services -->
<section class="abs services">
  <h2 class="section-title" style="top:52px">Our <span class="accent">Services</span></h2>
  <div class="divider" style="left:429px"></div>
  <div class="divider" style="left:781px"></div>

  <div class="service" style="left:73px">
    <svg class="icon" viewBox="0 0 124 124">
      <path d="M8 70 A54 54 0 0 0 116 70" fill="none" stroke="#e9b4ba" stroke-width="4"/>
      <circle cx="62" cy="58" r="54" fill="#c11f2f"/>
      <g fill="none" stroke="#fff" stroke-width="2.5">
        <circle cx="48" cy="40" r="6"/><circle cx="62" cy="36" r="6"/><circle cx="76" cy="40" r="6"/>
        <path d="M38 60c0-8 5-12 10-12s10 4 10 12M52 56c0-8 5-12 10-12s10 4 10 12M66 60c0-8 5-12 10-12s10 4 10 12"/>
        <path d="M32 72h14l10 6h12a4 4 0 0 1 0 8H54M70 84l16-8a4 4 0 0 1 4 6L68 94H40l-8-6"/>
      </g>
    </svg>
    <h3>Lorem ipsum dolor sited</h3>
    <p>Lorem ipsum dolor sit ameted consectetur adipiscing elit sed do eiusmod tempor incididunt ut labore et dolore magna aliquat enim ad minim veniam quis nostrud.</p>
    <a class="btn btn-outline">Learn More
      <svg class="dot-arrow" viewBox="0 0 16 16"><circle cx="8" cy="8" r="8" fill="#c11f2f"/><path d="M6.5 4.5 10 8l-3.5 3.5" stroke="#fff" stroke-width="2" fill="none"/></svg></a>
  </div>

  <div class="service" style="left:425px">
    <svg class="icon" viewBox="0 0 124 124">
      <path d="M8 70 A54 54 0 0 0 116 70" fill="none" stroke="#e9b4ba" stroke-width="4"/>
      <circle cx="62" cy="58" r="54" fill="#c11f2f"/>
      <g fill="none" stroke="#fff" stroke-width="2.5">
        <circle cx="54" cy="44" r="10"/>
        <path d="M34 90V74c0-8 8-12 20-12s20 4 20 12v16z"/>
        <path d="M50 62l4 28 4-28"/>
        <circle cx="80" cy="40" r="9"/>
        <path d="M80 34v12M77 37h5a2 2 0 0 1 0 4h-4a2 2 0 0 0 0 4h5"/>
      </g>
    </svg>
    <h3>Lorem ipsum dolor sited</h3>
    <p>Lorem ipsum dolor sit ameted consectetur adipiscing elit sed do eiusmod tempor incididunt ut labore et dolore magna aliquat enim ad minim veniam quis nostrud.</p>
    <a class="btn btn-outline">Learn More
      <svg class="dot-arrow" viewBox="0 0 16 16"><circle cx="8" cy="8" r="8" fill="#c11f2f"/><path d="M6.5 4.5 10 8l-3.5 3.5" stroke="#fff" stroke-width="2" fill="none"/></svg></a>
  </div>

  <div class="service" style="left:778px">
    <svg class="icon" viewBox="0 0 124 124">
      <path d="M8 70 A54 54 0 0 0 116 70" fill="none" stroke="#e9b4ba" stroke-width="4"/>
      <circle cx="62" cy="58" r="54" fill="#c11f2f"/>
      <g fill="none" stroke="#fff" stroke-width="2.5">
        <rect x="38" y="28" width="36" height="50" rx="2"/>
        <circle cx="48" cy="40" r="4"/>
        <path d="M56 38h12M56 44h10M44 54h24M44 61h24M44 68h16"/>
        <circle cx="80" cy="72" r="6"/>
        <path d="M70 94v-8c0-5 4-8 10-8s10 3 10 8v8"/>
      </g>
    </svg>
    <h3>Lorem ipsum dolor sited</h3>
    <p>Lorem ipsum dolor sit ameted consectetur adipiscing elit sed do eiusmod tempor incididunt ut labore et dolore magna aliquat enim ad minim veniam quis nostrud.</p>
    <a class="btn btn-outline">Learn More
      <svg class="dot-arrow" viewBox="0 0 16 16"><circle cx="8" cy="8" r="8" fill="#c11f2f"/><path d="M6.5 4.5 10 8l-3.5 3.5" stroke="#fff" stroke-width="2" fill="none"/></svg></a>
  </div>
</section>

<!-- find talent -->
<div class="abs talent-photo" role="img" aria-label="Team of colleagues collaborating around a table and whiteboard"></div>
<section class="abs talent-panel">
  <h2>Find Talent To Get<br>More Done</h2>
  <p>Lorem ipsum dolor sit amet, consectetur adipiscing elit, sed do eiusmod tempor incididunt ut labore et dolore magna aliqua. Ut enim ad minim veniam, quis nostrud exercitation ullamco laboris nisi ut aliquip ex ea commodo consequat. Duis aute irure dolor in reprehenderit in voluptate velit esse cillum dolore eu fugiat nulla pariatur. Excepteur sint occaecat cupidatat non proident, sunt in culpa qui officia deserunt.</p>
  <a class="btn btn-light" style="left:48px;top:395px;width:157px;height:48px">Learn More
    <svg class="dot-arrow" viewBox="0 0 16 16"><circle cx="8" cy="8" r="8" fill="#c11f2f"/><path d="M6.5 4.5 10 8l-3.5 3.5" stroke="#fff" stroke-width="2" fill="none"/></svg></a>
</section>

<!-- blog -->
<h2 class="section-title" style="top:2606px">News / <span class="accent">Blog</span></h2>

<article class="card" style="left:111px">
  <div class="thumb" role="img" aria-label="Two women reviewing documents at an interview desk" style="background:linear-gradient(135deg,#8f7a66,#e8e3dc 55%,#c7bdb0)"></div>
  <div class="meta">&#128197; Mar 01, 2024 &nbsp;|&nbsp; &#9679; By Nora Vell</div>
  <h3>Lorem ipsum dolor sit amet</h3>
  <p>Lorem ipsum dolor sit amet consectetur adipiscing elit sed do eiusmod tempor.</p>
  <div class="more">READ MORE <svg class="dot-arrow" viewBox="0 0 16 16"><circle cx="8" cy="8" r="8" fill="#c11f2f"/><path d="M6.5 4.5 10 8l-3.5 3.5" stroke="#fff" stroke-width="2" fill="none"/></svg></div>
</article>

<article class="card" style="left:446px">
  <div class="thumb" role="img" aria-label="Three coworkers smiling around a tablet" style="background:linear-gradient(135deg,#6b5a4a,#a99684 50%,#4a4a52)"></div>
  <div class="meta">&#128197; Mar 01, 2024 &nbsp;|&nbsp; &#9679; By Nora Vell</div>
  <h3>Lorem ipsum dolor sit amet</h3>
  <p>Lorem ipsum dolor sit amet consectetur adipiscing elit sed do eiusmod tempor.</p>
  <div class="more">READ MORE <svg class="dot-arrow" viewBox="0 0 16 16"><circle cx="8" cy="8" r="8" fill="#c11f2f"/><path d="M6.5 4.5 10 8l-3.5 3.5" stroke="#fff" stroke-width="2" fill="none"/></svg></div>
</article>

<article class="card" style="left:780px">
  <div class="thumb" role="img" aria-label="Business handshake over a desk with charts" style="background:linear-gradient(135deg,#3a4250,#9aa4ad 50%,#d5d9dc)"></div>
  <div class="meta">&#128197; Mar 01, 2024 &nbsp;|&nbsp; &#9679; By Nora Vell</div>
  <h3>Lorem ipsum dolor sit amet</h3>
  <p>Lorem ipsum dolor sit amet consectetur adipiscing elit sed do eiusmod tempor.</p>
  <div class="more">READ MORE <svg class="dot-arrow" viewBox="0 0 16 16"><circle cx="8" cy="8" r="8" fill="#c11f2f"/><path d="M6.5 4.5 10 8l-3.5 3.5" stroke="#fff" stroke-width="2" fill="none"/></svg></div>
</article>

<!-- contact -->
<section class="abs contact" role="img" aria-label="Faint city skyline backdrop in pink tones">
  <h2 class="section-title" style="top:60px">Contact <span class="accent">Us</span></h2>
  <div class="field" style="left:193px;top:140px;width:393px;height:51px">Enter Name</div>
  <div class="field" style="left:193px;top:207px;width:393px;height:51px">Email Address</div>
  <div class="field" style="left:193px;top:272px;width:393px;height:51px">Phone Number</div>
  <div class="field area" style="left:610px;top:140px;width:396px;height:185px">Message</div>
  <a class="btn btn-solid" style="left:521px;top:362px;width:156px;height:46px">Submit Now
    <svg class="dot-arrow" viewBox="0 0 16 16"><circle cx="8" cy="8" r="8" fill="#fff"/><path d="M6.5 4.5 10 8l-3.5 3.5" stroke="#c11f2f" stroke-width="2" fill="none"/></svg></a>
</section>

<!-- footer -->
<svg class="abs footer-shape" viewBox="0 0 1200 200" preserveAspectRatio="none">
  <path d="M0 158 L600 24 L1200 158 L1200 192 L600 36 L0 192 Z" fill="#c11f2f"/>
  <path d="M0 192 L600 36 L1200 192 L1200 200 L0 200 Z" fill="#262626"/>
  <circle cx="600" cy="51" r="26" fill="#fff"/>
  <path d="M591 54l9-8 9 8M591 62l9-8 9 8" stroke="#c11f2f" stroke-width="3" fill="none"/>
</svg>

<footer class="abs footer">
  <div class="foot-brand">
    <div class="mark"></div>
    <div class="name">keysteptalent</div>
  </div>

  <div class="foot-col" style="left:439px">
    <h4>Quick Links</h4>
    <ul><li>Home</li><li>About Us</li><li>Services</li><li>Testimonials</li><li>Blog</li><li>Contact Us</li></ul>
  </div>

  <div class="foot-col" style="left:666px;width:240px">
    <h4>Contact Us</h4>
    <div class="contact-line" style="margin-top:22px"><span class="ic"><svg width="11" height="11" viewBox="0 0 24 24" fill="#ddd"><path d="M6.6 10.8a15.1 15.1 0 0 0 6.6 6.6l2.2-2.2c.3-.3.7-.4 1-.2 1.1.4 2.3.6 3.6.6.6 0 1 .4 1 1V20c0 .6-.4 1-1 1A17 17 0 0 1 3 4c0-.6.4-1 1-1h3.5c.6 0 1 .4 1 1 0 1.3.2 2.5.6 3.6.1.3 0 .7-.2 1z"/></svg></span><span style="padding-top:3px">+1 888 888 8888</span></div>
    <div class="contact-line"><span class="ic"><svg width="11" height="9" viewBox="0 0 24 18" fill="#ddd"><path d="M0 0h24v18H0z M2 2v1l10 7 10-7V2z" fill-rule="evenodd"/></svg></span><span style="padding-top:3px">info@keysteptalent.com</span></div>
    <div class="contact-line"><span class="ic"><svg width="10" height="12" viewBox="0 0 20 26" fill="#ddd"><path d="M10 0a10 10 0 0 1 10 10c0 7-10 16-10 16S0 17 0 10A10 10 0 0 1 10 0zm0 6a4 4 0 1 0 0 8 4 4 0 0 0 0-8z" fill-rule="evenodd"/></svg></span><span>234,Lorem ipsum dolor sit consectetur adipiscing elit</span></div>
    <div class="contact-line"><span class="ic"><svg width="10" height="10" viewBox="0 0 20 20" fill="#ddd"><rect x="2" y="6" width="16" height="13" rx="2"/><rect x="5" y="1" width="10" height="6" rx="1"/></svg></span><span style="padding-top:3px">123-456-7890</span></div>
  </div>

  <div class="foot-col" style="left:954px">
    <h4>Other Links</h4>
    <ul><li>Specifications</li><li>Site Map</li><li>Terms of Use</li><li>Privacy Policy</li><li>Terms &amp; Condition</li></ul>
  </div>
</footer>

<div class="abs chat"><svg width="24" height="22" viewBox="0 0 24 22"><path d="M12 1C6 1 1 5 1 10c0 2.5 1.2 4.7 3.2 6.3L3 21l5-2.6c1.2.4 2.6.6 4 .6 6 0 11-4 11-9S18 1 12 1z" fill="#fff"/><circle cx="7.5" cy="10" r="1.5" fill="#c11f2f"/><circle cx="12" cy="10" r="1.5" fill="#c11f2f"/><circle cx="16.5" cy="10" r="1.5" fill="#c11f2f"/></svg></div>

<div class="abs bottom-bar">
  <div class="copy">Copyright© 2024 &nbsp;<u>Keystep Talent.</u> &nbsp;| &nbsp;All Rights Reserved</div>
  <span class="circ" style="left:984px"></span>
  <span class="circ" style="left:1021px"></span>
  <span class="circ" style="left:1058px"></span>
</div>

</body>
</html>
```